Fenwick Ridge Accounting - New client package

I need a stationary package (presentation folder cover, welcome letter template/design, sample financial report template/design, business card and new logo) for my accounting business. I would like to see designs that use the color blue. Financial icons can be included in the design. The final design should be clean and communicate professionalism and the use of modern; user-friendly technology. Attached postcard files should help with overall design concept.

```html
<!DOCTYPE html>
<html lang="en">
<head>
<meta charset="utf-8">
<title>Fenwick Ridge Accounting – Business Card</title>
<link rel="stylesheet" href="https://fonts.googleapis.com/css2?family=Roboto:wght@400;500&family=Saira+Condensed:wght@500&display=swap">
<style>
  :root {
    --stage: #191919;
    --card: #f9f9f9;
    --brand-blue: #2e5b8a;
    --slate: #3d4144;
    --ink: #3a3a3a;
  }
  * { box-sizing: border-box; margin: 0; padding: 0; }
  html, body { width: 1200px; height: 1200px; overflow: hidden; }
  body {
    position: relative;
    background: var(--stage);
    font-family: "Roboto", Arial, sans-serif;
    color: var(--ink);
  }
  .card {
    position: absolute;
    left: 318px;
    width: 562px;
    height: 339px;
    background: var(--card);
    overflow: hidden;
  }
  .card--front { top: 251px; }
  .card--back { top: 609px; }

  .brand-disc {
    position: absolute;
    width: 112px;
    height: 112px;
    border-radius: 50%;
    background: var(--brand-blue);
  }
  .brand-name {
    position: absolute;
    text-align: center;
    font-family: "Roboto", Arial, sans-serif;
    font-weight: 500;
    color: var(--brand-blue);
    text-transform: uppercase;
    line-height: 1.25;
  }

  /* front */
  .card--front .brand-disc { left: 225px; top: 64px; }
  .card--front .brand-name {
    left: 0; width: 100%; top: 186px;
    font-size: 26px; letter-spacing: 3px;
  }
  .card--front .brand-name .line-2 { letter-spacing: 11px; }
  .site-line {
    position: absolute;
    left: 0; width: 100%; top: 293px;
    display: flex; justify-content: center; align-items: center; gap: 16px;
    font-size: 13.5px; color: var(--ink);
  }
  .site-line .dash {
    width: 38px; height: 2px;
    background: var(--brand-blue);
    clip-path: polygon(0 50%, 30% 0, 100% 0, 100% 100%, 30% 100%);
  }
  .site-line .dash--right { transform: scaleX(-1); }
  .accent-bar {
    position: absolute; left: 0; bottom: 0;
    width: 100%; height: 14px; display: flex;
  }
  .accent-bar .seg-blue { flex: 1; background: var(--brand-blue); }
  .accent-bar .seg-slate { flex: 1; background: var(--slate); }

  /* back */
  .card--back .brand-disc { left: 94px; top: 87px; }
  .card--back .brand-name {
    left: 40px; width: 220px; top: 205px;
    font-size: 17px; letter-spacing: 1.5px;
  }
  .card--back .brand-name .line-2 { letter-spacing: 7px; }
  .holder {
    position: absolute; left: 298px; top: 100px;
  }
  .holder__name {
    font-family: "Saira Condensed", "Arial Narrow", sans-serif;
    font-weight: 500; font-size: 26px; line-height: 1;
    color: var(--brand-blue);
  }
  .holder__role { margin-top: 6px; font-size: 14px; color: var(--ink); }
  .contacts {
    position: absolute; left: 298px; top: 172px;
    list-style: none; font-size: 14px; color: var(--ink);
  }
  .contacts li {
    display: flex; align-items: center; gap: 8px;
    height: 21px;
  }
  .contacts svg { width: 14px; height: 14px; fill: var(--brand-blue); flex: none; }
</style>
</head>
<body>

<section class="card card--front" aria-label="Business card front">
  <div class="brand-disc"></div>
  <div class="brand-name"><div>Fenwick Ridge</div><div class="line-2">Accounting</div></div>
  <div class="site-line">
    <span class="dash"></span>
    <span>www.fenwickridgeaccounting.com</span>
    <span class="dash dash--right"></span>
  </div>
  <div class="accent-bar"><span class="seg-blue"></span><span class="seg-slate"></span></div>
</section>

<section class="card card--back" aria-label="Business card back">
  <div class="brand-disc"></div>
  <div class="brand-name"><div>Fenwick Ridge</div><div class="line-2">Accounting</div></div>

  <div class="holder">
    <div class="holder__name">Marian Holt</div>
    <div class="holder__role">Managing Director</div>
  </div>

  <ul class="contacts">
    <li>
      <svg viewBox="0 0 16 16" aria-hidden="true"><path d="M1 5c0-2 3-3 7-3s7 1 7 3v1h-3V4.5C11 4 9.5 4 8 4s-3 0-4 .5V6H1z"/><path d="M4 7h8l2 7H2z"/></svg>
      <span>1.877.555.0142</span>
    </li>
    <li>
      <svg viewBox="0 0 16 16" aria-hidden="true"><path d="M1 3h14v10H1z M2.5 4.5 8 9l5.5-4.5v7h-11z" fill-rule="evenodd"/></svg>
      <span>info@fenwickridgeaccounting.com</span>
    </li>
    <li>
      <svg viewBox="0 0 16 16" aria-hidden="true"><circle cx="8" cy="8" r="7"/><path d="M1 8h14M8 1v14M3 4h10M3 12h10" stroke="#f9f9f9" stroke-width="0.9" fill="none"/><ellipse cx="8" cy="8" rx="3" ry="7" stroke="#f9f9f9" stroke-width="0.9" fill="none"/></svg>
      <span>www.fenwickridgeaccounting.com</span>
    </li>
  </ul>
</section>

</body>
</html>
```